Luxury Wine Label for New Startup Winery

We need a wine label for our new winery startup. We have worked with a local designer but do not feel the resulting label / logo have the elevation required to present our brand as a luxury wine. Our winery is called "Quailbrook Vineyards" and we are focused on extremely high quality hand crafted artisan and estate wines from the Pacific Northwest.
We would like to see designs that utilize a tree line, or other imagery that represents the "Quailbrook" part of our company name. Another interesting feature could be wood grain.
A logo will be required based on your design so please design with this in mind:
This logo should be consistent with the wine bottle label design, and should be representative of our high end exclusive wine while giving a sense of place (Oregon/ Pacific Northwest.)
I will supply an image of the design we received from our local designer, PLEASE NOTE: in general we do like wood grain and tree line concepts but feel the execution was poorly done.
ATTN: Logo design should be suitable for use on: Bottles (Red wine/rose/white wine), Bussiness cards, vehicle signage, business signage, etc
P.S.:
If you have a design that is not outside the box we are still interested in seeing it.
Label is for a burgundy style bottle with a label height of 3.5 - 4" and a width of 3.5-4"
any label <= 4"x4" and >=3.5"x3.5" will be acceptable:
HOWEVER Width should be greater than or equal to height due to the bottle format
Target Market(s)
Wine enthusiasts with adequate discretionary budgets to afford $100 bottles of wine.
Industry/Entity Type
Wine / Winery
Requirements
Must have
- A sense of luxury, a feel of exclusivity, and a theme consistent with our product and brand name
Nice to have
- Tree line, wood grain or other wood themes. Serif fonts
Should not have
- anything cheesy, off topic, hard to read script fonts or anything that makes the label hard to read from a few feet away or too busy

```html
<!DOCTYPE html>
<html lang="en">
<head>
<meta charset="utf-8">
<title>Quailbrook Vineyards — Syrah Label</title>
<link rel="stylesheet" href="https://fonts.googleapis.com/css2?family=Cormorant+Garamond:wght@500;600&family=Great+Vibes&display=swap">
<style>
  :root {
    --backdrop: #241c1b;
    --label-black: #1d1e21;
    --label-black-deep: #141518;
    --gold: #c9a36a;
    --gold-bright: #e6cd97;
    --silver-line: #8d8f94;
  }
  html, body {
    margin: 0;
    padding: 0;
    width: 1200px;
    height: 1200px;
    overflow: hidden;
    background: var(--backdrop);
  }
  .canvas {
    position: relative;
    width: 1200px;
    height: 1200px;
    display: flex;
    align-items: center;
    justify-content: center;
  }
  .label {
    position: relative;
    width: 620px;
    height: 880px;
    background: var(--label-black-deep);
    display: flex;
    flex-direction: column;
    box-shadow: 0 20px 60px rgba(0,0,0,0.45);
  }
  .label__main {
    position: relative;
    height: 590px;
    background: linear-gradient(180deg, var(--label-black) 0%, #191a1d 100%);
    display: flex;
    flex-direction: column;
    align-items: center;
  }
  .rule {
    position: absolute;
    left: 0;
    right: 0;
    height: 1px;
    background: var(--silver-line);
    opacity: 0.7;
  }
  .rule--top { top: 28px; }
  .rule--bottom { bottom: 14px; }
  .brand-mark {
    margin-top: 150px;
    width: 34px;
    height: 34px;
    border: 1.5px solid var(--gold);
    border-radius: 50%;
  }
  .wordmark {
    margin: 60px 0 0;
    text-align: center;
    font-family: "Cormorant Garamond", "Times New Roman", serif;
    font-weight: 600;
    color: var(--gold);
    text-transform: uppercase;
    line-height: 1.25;
  }
  .wordmark__name {
    display: block;
    font-size: 42px;
    letter-spacing: 0.42em;
    margin-right: -0.42em;
  }
  .wordmark__sub {
    display: block;
    font-size: 34px;
    letter-spacing: 0.42em;
    margin-right: -0.42em;
  }
  .treeline {
    position: absolute;
    left: 75px;
    bottom: 28px;
    width: 440px;
    height: 80px;
  }
  .label__gap {
    position: relative;
    height: 32px;
    background: var(--label-black-deep);
  }
  .label__gap .rule { top: 12px; opacity: 0.45; }
  .label__band {
    position: relative;
    flex: 1;
    overflow: hidden;
  }
  .wood-grain {
    position: absolute;
    inset: 0;
    width: 100%;
    height: 100%;
  }
  .band__line {
    position: absolute;
    left: 0;
    right: 0;
    top: 32px;
    height: 2px;
    background: linear-gradient(90deg, transparent 0%, var(--gold) 20%, var(--gold-bright) 60%, var(--gold) 100%);
  }
  .varietal {
    position: absolute;
    top: 78px;
    left: 0;
    right: 0;
    margin: 0;
    text-align: center;
    font-family: "Great Vibes", cursive;
    font-weight: 400;
    font-size: 82px;
    color: var(--gold);
    line-height: 1;
  }
  .origin {
    position: absolute;
    left: 0;
    right: 0;
    bottom: 16px;
    margin: 0;
    display: flex;
    align-items: center;
    justify-content: center;
    font-family: "Cormorant Garamond", "Times New Roman", serif;
    font-weight: 500;
    font-size: 22px;
    color: var(--gold);
    letter-spacing: 0.02em;
  }
  .origin__dash {
    width: 60px;
    height: 1.5px;
    background: var(--gold);
  }
  .origin__item { padding: 0 16px; }
  .origin__divider {
    width: 1px;
    height: 28px;
    background: var(--gold);
    opacity: 0.8;
  }
</style>
</head>
<body>
<main class="canvas">
  <article class="label">
    <section class="label__main">
      <div class="rule rule--top"></div>
      <div class="brand-mark" aria-hidden="true"></div>
      <h1 class="wordmark">
        <span class="wordmark__name">Quailbrook</span>
        <span class="wordmark__sub">Vineyards</span>
      </h1>
      <svg class="treeline" role="img" aria-label="Gold foil silhouette of an evergreen tree line" viewBox="0 0 440 80" preserveAspectRatio="none">
        <defs>
          <linearGradient id="treeFoil" x1="0" y1="0" x2="1" y2="0">
            <stop offset="0" stop-color="#b8965c"/>
            <stop offset="0.45" stop-color="#8a7048"/>
            <stop offset="0.75" stop-color="#f1e2b8"/>
            <stop offset="1" stop-color="#c9a36a"/>
          </linearGradient>
        </defs>
        <rect x="0" y="0" width="440" height="80" fill="url(#treeFoil)" opacity="0.85"/>
      </svg>
      <div class="rule rule--bottom"></div>
    </section>
    <div class="label__gap"><div class="rule"></div></div>
    <section class="label__band">
      <svg class="wood-grain" role="img" aria-label="Deep red wood grain texture" viewBox="0 0 620 258" preserveAspectRatio="none">
        <defs>
          <linearGradient id="woodTone" x1="0" y1="0" x2="1" y2="0.3">
            <stop offset="0" stop-color="#1c1416"/>
            <stop offset="0.35" stop-color="#3a1619"/>
            <stop offset="0.7" stop-color="#6e2628"/>
            <stop offset="1" stop-color="#7a2a2c"/>
          </linearGradient>
        </defs>
        <rect width="620" height="258" fill="url(#woodTone)"/>
      </svg>
      <div class="band__line"></div>
      <h2 class="varietal">Syrah</h2>
      <p class="origin">
        <span class="origin__dash"></span>
        <span class="origin__item">PACIFIC</span>
        <span class="origin__divider"></span>
        <span class="origin__item">2025</span>
        <span class="origin__divider"></span>
        <span class="origin__item">NORTHWEST</span>
        <span class="origin__dash"></span>
      </p>
    </section>
  </article>
</main>
</body>
</html>
```